Non-profit organization needs newsletter

We are a non-profit organization that conducts medical missions overseas. We recently returned from a mission to Guangaje and San Isidro, Ecuador and need a newsletter describing our work to our supporters. We have a logo and would like the design to include the blue, green and white of the logo as well. The final design should be professional and communicate the culture of Ecuador using the photos of the people we helped and their corresponding stories
Updates

Reason: I NEED SOME SMALL CHANGES TO SOME DESIGN.

Target Market(s)

Prospective donors to our organization

Industry/Entity Type

Non Profit

Font styles to use
Sans Serif

Colors
9bcb3c
0456a4

Requirements
Must have
• 2 page newsletter, logo must be on the front page. Front page must feature pictures of the village of Guangaje and the text description. Front page must have the words GLOBAL VOLUNTEERISM COMPASSION ALTRUISM across the top of the page. Bottom of front page must have text that thanks donors for their support. Back page must have website address along the bottom. New hospital picture and text must be on back page. Pictures of patients and the corresponding text should be on the bottom of front page and also on the back page. Color theme is same colors in logo
Nice to have
• Pictures of random people can be untitled and just scattered throughout the newsletter.
Should not have
• Techno or modern design or non traditional font.

```html
<!DOCTYPE html>
<html lang="en">
<head>
<meta charset="utf-8">
<title>Andes Care Collective Newsletter</title>
<link href="https://fonts.googleapis.com/css2?family=Arimo:ital,wght@0,400;1,700&family=Crimson+Text:ital,wght@0,400;1,400&family=Marcellus&display=swap" rel="stylesheet">
<style>
:root{
  --blue:#0456a4;
  --blue-deep:#1f4c8f;
  --green:#2f7a3b;
  --green-band:#3f7a3a;
  --lime:#9bcb3c;
  --ink:#1c1c1c;
  --page:#ffffff;
  --box:#e8ece3;
  --rule:#9aa3a8;
  --mist:#dfe3df;
}
*{box-sizing:border-box;margin:0;padding:0}
html,body{width:1200px;height:777px;overflow:hidden;background:#fff}
.spread{position:relative;width:1200px;height:777px}
.page{position:absolute;top:12px;height:754px;border:1px solid #444;background:linear-gradient(to bottom,var(--page) 45%,var(--mist) 100%);overflow:hidden}
.page--front{left:12px;width:583px}
.page--back{left:606px;width:584px}
.abs{position:absolute}
.photo{position:absolute;box-shadow:0 1px 4px rgba(0,0,0,.45);border:3px solid #fff}

.banner{left:34px;top:32px;width:514px;height:32px;background:linear-gradient(to right,var(--blue-deep) 0%,#3b6db0 65%,rgba(59,109,176,0) 100%);color:#fff;font-family:"Marcellus",serif;font-size:15.5px;letter-spacing:.5px;display:flex;align-items:center;padding-left:50px}

.brand{left:52px;top:96px;width:230px;text-align:center;font-family:"Arimo",sans-serif;color:var(--blue)}
.brand__dot{width:46px;height:46px;border-radius:50%;background:var(--blue);margin:0 auto 16px}
.brand__name{font-size:21px;line-height:1.15;letter-spacing:1px}

.intro{left:290px;top:92px;width:262px;border-top:1px solid var(--rule);border-bottom:1px solid var(--rule);padding:8px 0 9px;font-family:"Arimo",sans-serif;font-style:italic;font-weight:700;color:var(--blue);font-size:14.3px;line-height:21px;text-align:center}

.body{font-family:"Arimo",sans-serif;color:var(--ink);font-size:11.7px;line-height:15px;text-align:justify}
.body--one{left:50px;top:481px;width:488px}
.body--two{left:50px;top:547px;width:290px;text-indent:22px}
.thanks{left:48px;top:716px;width:500px;font-family:"Crimson Text",serif;font-style:italic;color:var(--blue);font-size:14px}

.story{position:absolute;background:var(--box);box-shadow:0 1px 3px rgba(0,0,0,.35)}
.story__text{position:absolute;font-family:"Crimson Text",serif;color:var(--ink);font-size:10px;line-height:12.6px;text-align:justify}

.divider{left:48px;top:432px;width:490px;height:1px;background:linear-gradient(to right,rgba(0,0,0,0),#777,rgba(0,0,0,0))}
.hospital-text{left:268px;top:456px;width:268px;font-family:"Crimson Text",serif;font-size:12.6px;line-height:18.6px;color:var(--ink);text-align:justify;text-indent:12px}
.follow{left:62px;top:624px;font-family:"Crimson Text",serif;font-style:italic;font-size:15px;color:var(--blue)}
.social{position:absolute;top:644px;width:34px;height:34px;border-radius:50%;border:2px solid #fff;box-shadow:0 0 0 1px #999}
.social--one{left:48px;background:var(--blue)}
.social--two{left:90px;background:#c2185b}
.follow-name{left:134px;top:651px;font-family:"Arimo",sans-serif;font-size:16px;color:var(--blue);letter-spacing:.5px}
.badge{left:380px;top:576px;width:140px;height:100px;background:#fff;border-radius:9px;box-shadow:0 1px 5px rgba(0,0,0,.45);text-align:center;font-family:"Arimo",sans-serif;color:var(--blue);padding-top:20px}
.badge__dot{width:24px;height:24px;border-radius:50%;background:var(--blue);margin:0 auto 9px}
.badge__name{font-size:11px;line-height:13px;letter-spacing:.5px}
.web{left:48px;top:690px;width:496px;height:32px;background:linear-gradient(to right,rgba(63,122,58,.55),var(--green-band) 20%,var(--green-band) 80%,rgba(63,122,58,.55));color:#fff;font-family:"Marcellus",serif;font-size:16.5px;letter-spacing:1px;display:flex;align-items:center;justify-content:center}
</style>
</head>
<body>
<div class="spread">

  <section class="page page--front">
    <div class="abs banner">GLOBAL VOLUNTEERISM ♦ COMPASSION ♦ ALTRUISM</div>

    <div class="abs brand">
      <div class="brand__dot"></div>
      <div class="brand__name">ANDES CARE<br>COLLECTIVE</div>
    </div>

    <p class="abs intro">The Andes Care Collective team partners again with Wayfarer Health to provide specialty surgical care to the indigent mestizos people of the small village of Guangaje, Ecuador.</p>

    <div class="photo" role="img" aria-label="Market square in Guangaje with a pink church bell tower and vendors' stalls" style="left:50px;top:255px;width:324px;height:216px;background:linear-gradient(to bottom,#6d9fd6 0%,#b9d1ea 35%,#c9a6a0 55%,#6e6a6a 80%,#8b8478 100%)"></div>
    <div class="photo" role="img" aria-label="Hillside houses of Guangaje under a cloudy sky" style="left:374px;top:255px;width:164px;height:108px;background:linear-gradient(to bottom,#5f8fd0 0%,#c9d9ec 40%,#9a9478 65%,#c8b99a 100%)"></div>
    <div class="photo" role="img" aria-label="Village information centre wall sign" style="left:374px;top:363px;width:164px;height:108px;background:linear-gradient(to bottom,#e3e1dc 0%,#f1f0ec 45%,#ffffff 70%,#d8dcd8 100%)"></div>

    <p class="abs body body--one">The town of Guangaje was established in 1861. The population, being 95% indigenous Indians, used to work for Spanish estates until they themselves became landowners. It presently has a population of just over 7000 people, but lacks basic services like potable water, sewage systems, advanced educational programs, and in some areas, electricity.</p>
    <p class="abs body body--two">Guangaje does have a small Health Center and a church, St. John the Baptist. Wayfarer Health provides medical services to people in remote villages like Guangaje and then partners with volunteer organizations like ACC to provide specialty surgical care. The ACC Team travelled to Guangaje to conduct a surgical clinic. We then assisted Wayfarer in transporting the villagers in need of surgery to the Valle Alto Regional Hospital in San Isidro, about 2 hours away, where the Team performed the surgery.</p>

    <div class="photo" role="img" aria-label="Villagers waiting in the clinic hall" style="left:351px;top:548px;width:184px;height:78px;transform:rotate(2deg);background:linear-gradient(to bottom,#d9e3e6 0%,#b7c4c6 45%,#5c4a44 75%,#7a6a60 100%)"></div>
    <div class="photo" role="img" aria-label="Patient in a red striped poncho and surgical cap" style="left:349px;top:628px;width:106px;height:80px;transform:rotate(-5deg);background:linear-gradient(to bottom,#7fb6d8 0%,#b88a6c 40%,#c03a37 70%,#9d2b2a 100%)"></div>

    <p class="abs thanks">Thank you to all our Friends and Family whose contributions made this mission possible.</p>
  </section>

  <section class="page page--back">
    <div class="story" style="left:48px;top:32px;width:488px;height:52px">
      <p class="story__text" style="left:8px;top:6px;width:384px">This is Mateo Andrés, a 1-year old who lives with his Mom in Guangaje. Mateo presented to us with an enlarging mass behind his left ear that was causing him pain and concern to his Mom. The ACC Team successfully removed the mass and a full recovery is anticipated.</p>
    </div>
    <div class="photo" role="img" aria-label="Toddler in a blue surgical gown and cap" style="left:446px;top:40px;width:82px;height:118px;background:linear-gradient(to bottom,#6ea3cf 0%,#3d7fc0 40%,#c9a58c 55%,#3f7fc4 100%)"></div>

    <div class="story" style="left:48px;top:90px;width:384px;height:74px">
      <div class="photo" role="img" aria-label="Patient lying in the operating room" style="left:6px;top:6px;width:134px;height:60px;background:linear-gradient(to right,#4f7fa8 0%,#8fb2c9 45%,#2d5d8a 100%)"></div>
      <p class="story__text" style="left:148px;top:6px;width:230px">45-year old Luis Ernesto lives in a remote village outside of Guangaje. He travelled 4 hours to have the ACC Team evaluate a large scalp mass causing him significant pain. We were able to successfully remove the mass, allowing Luis to return to work on his farm pain free.</p>
    </div>

    <div class="story" style="left:48px;top:174px;width:488px;height:88px">
      <p class="story__text" style="left:132px;top:6px;width:238px">The ACC Team had the opportunity to help treat Sofía Elena, a 4-year old girl who suffered burns to half her body when her family was burning garbage to stay warm. We instructed the hospital staff on burn care and provided specialized dressings donated to us by our supporters back home.</p>
    </div>
    <div class="photo" role="img" aria-label="Young girl resting in a hospital bed with dressings" style="left:56px;top:182px;width:116px;height:114px;background:linear-gradient(to bottom,#c9c6c8 0%,#9e8aa6 40%,#e8e2e0 70%,#8f8ea0 100%)"></div>
    <div class="photo" role="img" aria-label="Bandaged arm being treated for burns" style="left:422px;top:182px;width:106px;height:72px;background:linear-gradient(to right,#3f9fa5 0%,#c69a88 55%,#5fb0b3 100%)"></div>

    <div class="story" style="left:186px;top:270px;width:350px;height:74px">
      <p class="story__text" style="left:8px;top:6px;width:212px">54 year-old Pedro Ruiz from Guangaje presented to the ACC Team suffering for many years with a tumor above his right eye, which impeded his vision and caused him pain. We were able to successfully remove the mass and expect Pedro to recover fully.</p>
      <div class="photo" role="img" aria-label="Older man in a blue surgical cap after treatment" style="left:226px;top:6px;width:116px;height:62px;background:linear-gradient(to right,#5d8fc2 0%,#b07c62 50%,#8a5d48 100%)"></div>
    </div>

    <div class="story" style="left:48px;top:352px;width:488px;height:76px">
      <p class="story__text" style="left:132px;top:8px;width:348px">This is 5 year-old Lucía Paz from Guangaje who has suffered from a facial rash for several months. Many local doctors have seen her but none have been able to successfully treat her. The ACC Team saw her and outlined a treatment plan of a topical cream and oral medication which will finally resolve the rash.</p>
    </div>
    <div class="photo" role="img" aria-label="Little girl in a pink knitted hat" style="left:56px;top:320px;width:116px;height:90px;background:linear-gradient(to bottom,#d84a8c 0%,#3aa7b5 35%,#b88670 60%,#e0d8d6 100%)"></div>

    <div class="abs divider"></div>

    <div class="photo" role="img" aria-label="New red and glass regional hospital building" style="left:32px;top:450px;width:220px;height:146px;background:linear-gradient(to bottom,#4a7fc7 0%,#a9c4e6 35%,#c6283a 55%,#9fb2c0 85%,#c8d0d4 100%)"></div>
    <p class="abs hospital-text">This is the new Valle Alto Regional Hospital in San Isidro, planned to be open in the next several months. It is adjacent to the old hospital and built to better serve the nearly 100K inhabitants of the Sierra Alta province. The ACC Team looks forward to working there during our mission next year.</p>

    <p class="abs follow">Please follow us on Photogram and Friendbook:</p>
    <div class="social social--one"></div>
    <div class="social social--two"></div>
    <div class="abs follow-name">ANDES CARE COLLECTIVE</div>

    <div class="abs badge">
      <div class="badge__dot"></div>
      <div class="badge__name">ANDES CARE<br>COLLECTIVE</div>
    </div>

    <div class="abs web">WWW.ANDESCARECOLLECTIVE.ORG</div>
  </section>

</div>
</body>
</html>
```